Book Title: The Weaver's Lantern. Author Name: Maribel Trowcastle

We are needing a cover, spine and back cover design for a poetry book that we are publishing called The Weaver's Lantern. We are looking for an elegant, and simplistic design with a very natural, dynamic and powerful impact.

Design Idea #1 - Shiva Conch Shell with a pink or black background. See Paul Renwick Image attached for design inspiration. Simple and dynamic .
Title and Author name created in same style as the attached Paul Renwick's Harbors and Lanterns image.

Design Idea #2 - Image of cauldron on (see cauldrons attached for ideas) black background.
See Paul Renwick Image attached for design inspiration. Simple and dynamic Title and Author name created in same style as the attached Paul Renwick's Harbors and Lanterns image

Design Idea #3 - Image of Tree of Life (see attached images for idea of what we are looking for) Would like to see on plain white, green, black and green background.

Target Market(s)

Spiritual Women, healers, visionaries,Goddess'

Requirements
Must have
• Please see project descriptions for specific design concepts we are looking for. Please include the authors name: Maribel Trowcastle on front, spine and back cover of the book

```html
<!DOCTYPE html>
<html lang="en">
<head>
<meta charset="utf-8">
<title>The Weaver's Lantern — Spine and Front Cover</title>
<link rel="stylesheet" href="https://fonts.googleapis.com/css2?family=Old+Standard+TT:wght@400;700&display=swap">
<style>
  :root {
    --page-bg: #ffffff;
    --cover-black: #030303;
    --cover-sheen: #2a2a2a;
    --spine-black: #060606;
    --spine-edge: #1a1a1a;
    --type-white: #f7f7f4;
    --shell-light: #f1f2ee;
    --shell-mid: #c9cdc6;
    --shell-warm: #dccab3;
  }
  html, body {
    margin: 0;
    padding: 0;
    width: 1200px;
    height: 1200px;
    overflow: hidden;
    background: var(--page-bg);
  }
  .canvas {
    width: 1200px;
    height: 1200px;
    display: flex;
    align-items: center;
    justify-content: center;
  }
  .book {
    display: flex;
    height: 1120px;
    font-family: "Old Standard TT", "Times New Roman", serif;
    color: var(--type-white);
  }

  /* Spine */
  .spine {
    position: relative;
    width: 72px;
    height: 100%;
    background: linear-gradient(90deg, var(--spine-black) 0%, var(--spine-edge) 88%, var(--spine-black) 100%);
  }
  .spine-author,
  .spine-title {
    position: absolute;
    left: 50%;
    margin: 0;
    font-weight: 400;
    writing-mode: vertical-rl;
    transform: translateX(-50%);
    white-space: nowrap;
  }
  .spine-author {
    top: 84px;
    font-size: 20px;
    line-height: 1.05;
    letter-spacing: 0.16em;
    text-transform: uppercase;
  }
  .spine-title {
    top: 560px;
    font-size: 25px;
    letter-spacing: 0.08em;
  }

  /* Front cover */
  .front-cover {
    position: relative;
    width: 740px;
    height: 100%;
    background: radial-gradient(ellipse at 0% 0%, var(--cover-sheen) 0%, var(--cover-black) 42%);
  }
  .author-name {
    position: absolute;
    top: 128px;
    left: 0;
    right: 0;
    margin: 0;
    text-align: center;
    font-weight: 400;
    font-size: 52px;
    line-height: 1.45;
    letter-spacing: 0.14em;
    text-transform: uppercase;
  }
  .cover-image {
    position: absolute;
    top: 450px;
    left: 50%;
    width: 122px;
    height: 230px;
    transform: translateX(-50%);
  }
  .book-title {
    position: absolute;
    top: 858px;
    left: 0;
    right: 0;
    margin: 0;
    text-align: center;
    font-weight: 400;
    font-size: 80px;
    line-height: 1.18;
    letter-spacing: 0.05em;
  }
</style>
</head>
<body>
  <main class="canvas">
    <div class="book">
      <aside class="spine">
        <p class="spine-author">Maribel<br>Trowcastle</p>
        <p class="spine-title">The Weaver's Lantern</p>
      </aside>

      <section class="front-cover">
        <h2 class="author-name">Maribel<br>Trowcastle</h2>

        <svg class="cover-image" viewBox="0 0 122 230" role="img" aria-label="Photograph of a single white conch shell, point upward, lit against the black cover">
          <defs>
            <radialGradient id="shell-tone" cx="45%" cy="65%" r="60%">
              <stop offset="0%" stop-color="var(--shell-light)"/>
              <stop offset="70%" stop-color="var(--shell-mid)"/>
              <stop offset="100%" stop-color="var(--shell-warm)"/>
            </radialGradient>
          </defs>
          <path d="M72 2 C64 36 18 80 8 138 C0 186 32 228 60 228 C94 228 120 190 114 148 C108 104 82 64 72 2 Z" fill="url(#shell-tone)"/>
        </svg>

        <h1 class="book-title">The Weaver's<br>Lantern</h1>
      </section>
    </div>
  </main>
</body>
</html>
```